Hollendorf Business Card

This is the personal business card for Dr Mark Hollendorf and convers three area of his professional activity - all of them involve (foreign) languages:
o QRVB International Ltd - A translation company with 50 staff. Trades internationally
o WideHarbor Ltd - a global online auction marketplace for translation services (startup)
o Tonal Mosaic - cutting edge technology from the brain sciences which helps learners assimilate the sound patterns of a new language (startup)

Target Market(s)

The card needs to have a "cutting edge" feel - but for a fairly conservative audience - academics, investors.

Industry/Entity Type

Business

Requirements
Must have
• Text:
Dr Mark Hollendorf

Co-founder QRVB International Ltd (Language translation)
Founder WideHarbor Ltd (Translation marketplace)
Founder Tonal Mosaic (Language acquisition)

email: mark.oswin@velmora.co.nz
Phone: +64 21 596 3172
Twitter: @MarkOswin7

```html
<!DOCTYPE html>
<html lang="en">
<head>
<meta charset="utf-8">
<title>Dr Mark Hollendorf – Business Card</title>
<link rel="stylesheet" href="https://fonts.googleapis.com/css2?family=Arimo&family=Tinos:wght@700&display=swap">
<style>
  :root {
    --band: #6666cc;
    --frame: #4f9a9a;
    --ink: #111111;
    --name: #5a5ab4;
    --paper: #ffffff;
  }
  html, body {
    margin: 0;
    padding: 0;
    overflow: hidden;
    background: var(--paper);
  }
  .card {
    position: relative;
    width: 1200px;
    height: 686px;
    background: var(--paper);
    overflow: hidden;
  }
  .card-shapes {
    position: absolute;
    inset: 0;
  }
  .band-title {
    position: absolute;
    left: 98px;
    top: 104px;
    margin: 0;
    font-family: "Tinos", "Times New Roman", serif;
    font-weight: 700;
    font-size: 28px;
    letter-spacing: 0.5px;
    color: var(--paper);
  }
  .identity {
    position: absolute;
    left: 157px;
    top: 214px;
    font-family: "Arimo", Arial, sans-serif;
  }
  .identity-name {
    margin: 0;
    font-size: 31px;
    font-weight: 400;
    color: var(--name);
    line-height: 1;
  }
  .identity-role {
    margin: 28px 0 0;
    font-size: 26px;
    color: var(--ink);
    line-height: 1;
  }
  .ventures {
    position: absolute;
    left: 157px;
    top: 443px;
    width: 450px;
    margin: 0;
    padding: 0;
    list-style: none;
    font-family: "Tinos", "Times New Roman", serif;
    font-weight: 700;
    font-size: 18px;
    line-height: 27px;
    color: var(--ink);
  }
  .ventures li + li {
    margin-top: 21px;
  }
  .contact {
    position: absolute;
    left: 664px;
    top: 446px;
    margin: 0;
    font-family: "Arimo", Arial, sans-serif;
    font-size: 27px;
    line-height: 34px;
    color: var(--ink);
    font-style: normal;
  }
  .contact p {
    margin: 0;
  }
</style>
</head>
<body>
  <main class="card">
    <svg class="card-shapes" width="1200" height="686" viewBox="0 0 1200 686" aria-hidden="true">
      <!-- outer frame -->
      <path d="M94 190 V600 Q94 652 146 652 H1130 Q1193 652 1193 590 V185 Q1193 120 1120 120"
            fill="none" stroke="var(--frame)" stroke-width="4"/>
      <!-- title band -->
      <path d="M35 41 H1026 A80 80 0 0 1 1026 201 H35 Z" fill="var(--band)"/>
      <!-- rule across the band -->
      <rect x="82" y="152" width="926" height="6" fill="var(--paper)"/>
      <!-- name panel -->
      <rect x="136" y="201" width="773" height="135" fill="var(--paper)" stroke="var(--frame)" stroke-width="4"/>
    </svg>

    <h1 class="band-title">DR. MARK HOLLENDORF</h1>

    <section class="identity">
      <p class="identity-name">Mark Hollendorf</p>
      <p class="identity-role">Profession in Foreign Languages</p>
    </section>

    <ul class="ventures">
      <li>Co-founder QRVB International Ltd (Language<br>Translation)</li>
      <li>Founder WideHarbor Ltd (Translation<br>Marketplace)</li>
      <li>Founder Tonal Mosaic (Language Acquisition)</li>
    </ul>

    <address class="contact">
      <p>Phone: +64 21 596 3172</p>
      <p>Twitter: @MarkOswin7</p>
      <p>E-mail: mark.oswin@velmora.co.nz</p>
    </address>
  </main>
</body>
</html>
```